Boutique custom software development company needs new business card

Our nearly 20 year old custom software development company would like to better include the fact that we are now providing Bitcoin services. These new services are B2B include education (how to acquire and securely hold Bitcoin) and integrating Bitcoin payments into existing ecommerce sites or other existing systems. Please keep the card clean and simple. Attached is our current design and some other files. vextorial.com

Target Market(s)

businesses owners interested in long term relationship

Industry/Entity Type

Custom software development and Bitcoin

Contact Information for Business Card

Dale Parker, dale@vextorial.com, vextorial.com, (888) 555-VXTRL

Font styles to use
Other font styles liked:
• monospace

Requirements
Must have
• double-sided
Nice to have
• clean and simple
Should not have
• physical address

```html
<!DOCTYPE html>
<html lang="en">
<head>
<meta charset="utf-8">
<title>Vextorial business card</title>
<link href="https://fonts.googleapis.com/css2?family=Montserrat:wght@400;600&family=Lato:wght@300&display=swap" rel="stylesheet">
<style>
  :root {
    --bg: #2d2826;
    --card: #1f1f20;
    --card-edge: #2a2a2b;
    --orange: #ef8a3c;
    --blue: #5585c8;
    --white: #f4f4f4;
  }
  * { margin: 0; padding: 0; box-sizing: border-box; }
  html, body {
    width: 1200px; height: 716px; overflow: hidden;
    background: var(--bg);
  }
  .canvas {
    position: relative; width: 1200px; height: 716px;
    display: flex; align-items: center; justify-content: center; gap: 44px;
  }
  .card {
    position: relative; width: 540px; height: 309px;
    background: linear-gradient(135deg, var(--card-edge), var(--card) 60%);
    border-radius: 8px;
    box-shadow: 0 18px 40px rgba(0,0,0,.45);
    overflow: hidden;
  }
  /* front */
  .card-front { display: flex; flex-direction: column; align-items: center; justify-content: center; }
  .wordmark {
    font-family: "Montserrat", sans-serif; font-weight: 600;
    font-size: 58px; letter-spacing: 1px; color: var(--blue); line-height: 1;
  }
  .tagline {
    font-family: "Lato", sans-serif; font-weight: 300;
    font-size: 19px; color: var(--blue); margin-top: 8px; text-align: center; line-height: 1.35;
  }
  .tagline .services { color: var(--orange); }
  /* back */
  .card-back { display: flex; align-items: center; padding: 0 36px 0 44px; gap: 32px; }
  .brand-block { display: flex; flex-direction: column; align-items: center; gap: 12px; flex: none; }
  .brand-square { width: 170px; height: 170px; background: var(--blue); }
  .brand-name {
    font-family: "Montserrat", sans-serif; font-weight: 600;
    font-size: 17px; letter-spacing: 2px; color: var(--white);
  }
  .contact { font-family: "Montserrat", sans-serif; color: var(--white); }
  .person-name { font-size: 21px; font-weight: 600; letter-spacing: .5px; line-height: 1.1; }
  .person-name .first { color: var(--orange); }
  .person-name .last { color: var(--blue); }
  .person-title { font-size: 13px; letter-spacing: 1px; margin: 2px 0 8px; }
  .services-list { font-size: 13px; line-height: 1.45; margin-bottom: 6px; }
  .contact-line { display: flex; align-items: center; gap: 7px; font-size: 13px; line-height: 1.6; }
  .contact-line svg { width: 11px; height: 11px; flex: none; }
  .site-accent { color: var(--blue); }
</style>
</head>
<body>
<main class="canvas">
  <section class="card card-front" aria-label="Card front">
    <div class="wordmark">VEXTORIAL</div>
    <div class="tagline">developer of custom applications<br><span class="services">&amp; bitcoin services</span></div>
  </section>

  <section class="card card-back" aria-label="Card back">
    <div class="brand-block">
      <div class="brand-square"></div>
      <div class="brand-name">VEXTORIAL</div>
    </div>
    <div class="contact">
      <div class="person-name"><span class="first">DALE</span> <span class="last">PARKER</span></div>
      <div class="person-title">DIRECTOR</div>
      <div class="services-list">Custom Software<br>Bitcoin Education<br>Bitcoin Payments</div>
      <div class="contact-line">
        <svg viewBox="0 0 12 12" fill="none" stroke="#5585c8" stroke-width="1.3"><path d="M2.5 1.5h2l1 2.5-1.3 1a6 6 0 0 0 2.8 2.8l1-1.3 2.5 1v2a1 1 0 0 1-1 1A9 9 0 0 1 1.5 2.5a1 1 0 0 1 1-1z"/></svg>
        <span>(888) 555-VXTRL</span>
      </div>
      <div class="contact-line">
        <svg viewBox="0 0 12 12" fill="none" stroke="#5585c8" stroke-width="1.2"><rect x="1" y="2.5" width="10" height="7"/><path d="M1 2.5l5 4 5-4"/></svg>
        <span>dale@vextorial.com</span>
      </div>
      <div class="contact-line">
        <svg viewBox="0 0 12 12" fill="none" stroke="#5585c8" stroke-width="1.1"><circle cx="6" cy="6" r="5"/><ellipse cx="6" cy="6" rx="2.2" ry="5"/><path d="M1 6h10"/></svg>
        <span>www.<span class="site-accent">vextorial</span>.com</span>
      </div>
    </div>
  </section>
</main>
</body>
</html>
```